Seasonal Produce Calender Design

Design a seasonal fruit and vegetable calender made ready to print in various sizes. fruits and vegetables to be categorised into moths they are in season. File provided with content. Design is to flow with current company Logo, colours and brand identity. Can provide designers with link to similar calenders.

Please see link this is what im after:

https://www.brelvinharte.com.au/wp-content/uploads/2018/07/Seasonal-Calendar-Alts.jpg

Font styles to use
Serif

Colors

Designer to choose colors to be used in the design.

```html
<!DOCTYPE html>
<html lang="en">
<head>
<meta charset="utf-8">
<title>Seasonal Fruit, Vegetable, Herbs &amp; Spices Calendar</title>
<link href="https://fonts.googleapis.com/css2?family=Fredoka:wght@600;700&family=Arimo:wght@400&display=swap" rel="stylesheet">
<style>
:root{
  --summer:#ef9aa6;--autumn:#ecd4ab;--winter:#b9c8d2;--spring:#cfe0b0;
  --summer-ink:#c8394e;--autumn-ink:#85672e;--winter-ink:#55687a;--spring-ink:#3f8a28;
  --fruit:#f7c68a;--veg:#8fa67f;--herb:#d5c2b8;
  --ink:#111;--paper:#fff;--title-edge:#2a1a14;
}
*{box-sizing:border-box;margin:0;padding:0}
html,body{width:1200px;height:764px;overflow:hidden}
body{position:relative;font-family:"Arimo",Arial,sans-serif;color:var(--ink);background:#8a5a3a}
.backdrop{position:absolute;inset:0;background:
  radial-gradient(circle at 15% 20%,#7fae4a 0,transparent 28%),
  radial-gradient(circle at 80% 10%,#d9493a 0,transparent 30%),
  radial-gradient(circle at 30% 70%,#c93b2e 0,transparent 30%),
  radial-gradient(circle at 95% 60%,#a83347 0,transparent 30%),
  radial-gradient(circle at 5% 90%,#5f8f3a 0,transparent 25%),
  linear-gradient(135deg,#b0503a,#c7873f 40%,#8e3b3b 70%,#6c8a3d)}
.title-line{position:absolute;right:795px;font-family:"Fredoka",sans-serif;font-weight:700;color:var(--paper);line-height:1;white-space:nowrap;
  text-shadow:2px 0 0 var(--title-edge),-2px 0 0 var(--title-edge),0 2px 0 var(--title-edge),0 -2px 0 var(--title-edge),3px 4px 3px rgba(0,0,0,.5)}
.title-big{font-size:54px;letter-spacing:-1.5px}
.title-mid{font-size:44px}
.legend{position:absolute;left:26px;top:122px;display:flex;gap:3px}
.legend span{width:43px;height:43px;border-radius:50%;display:flex;align-items:center;justify-content:center;font-size:10.5px;color:#222}
.legend .s{background:var(--summer)}.legend .a{background:var(--autumn)}.legend .w{background:var(--winter)}.legend .p{background:var(--spring)}
.brand{position:absolute;left:30px;top:318px;display:flex;align-items:center;gap:8px;
  font-family:"Fredoka",sans-serif;font-weight:600;font-size:19px;line-height:1;color:var(--paper);white-space:nowrap}
.brand-dot{width:14px;height:14px;border-radius:50%;background:var(--spring)}
.chart{position:absolute;background:var(--paper);box-shadow:2px 3px 6px rgba(0,0,0,.5)}
.chart table{width:100%;border-collapse:collapse;table-layout:fixed}
.chart thead th{height:56px;font-weight:400;border-right:1px solid rgba(0,0,0,.25)}
.chart thead th.cat{font-family:"Fredoka",sans-serif;font-weight:600;font-size:17px;text-align:center}
.chart thead th.season span{display:inline-block;writing-mode:vertical-rl;transform:rotate(180deg);font-size:7.5px;line-height:1.1;text-align:center}
.chart tbody tr{height:11.8px}
.chart tbody th{font-weight:400;text-align:left;font-size:7.6px;padding-left:3px;white-space:nowrap;overflow:hidden;border-bottom:1px solid rgba(255,255,255,.6)}
.chart tbody td{text-align:center;font-size:7.6px;color:var(--ink);background:var(--paper);border-bottom:1px solid rgba(255,255,255,.8)}
.chart th.sm{color:var(--summer-ink);background:var(--summer)}
.chart th.au{color:var(--autumn-ink);background:var(--autumn)}
.chart th.wi{color:var(--winter-ink);background:var(--winter)}
.chart th.sp{color:var(--spring-ink);background:var(--spring)}
.chart tbody td:nth-child(2):empty:not(.w){background:var(--summer)}
.chart tbody td:nth-child(3):empty:not(.w){background:var(--autumn)}
.chart tbody td:nth-child(4):empty:not(.w){background:var(--winter)}
.chart tbody td:nth-child(5):empty:not(.w){background:var(--spring)}
.chart small{font-size:5.5px}
.fruits{left:418px;top:20px;width:364px;height:729px}
.fruits thead th.cat,.fruits tbody th{background:var(--fruit)}
.veg{left:805px;top:20px;width:363px;height:729px}
.veg thead th.cat,.veg tbody th{background:var(--veg)}
.herbs{left:33px;top:492px;width:363px;height:258px}
.herbs thead th{height:57px}
.herbs thead th.cat,.herbs tbody th{background:var(--herb)}
col.name{width:189px}
</style>
</head>
<body>
<div class="backdrop" role="img" aria-label="Photographic backdrop of fresh fruit and vegetables: apples, strawberries, grapes, broccoli, tomatoes and berries"></div>

<div class="title-line title-big" style="top:44px">SEASONAL</div>
<div class="title-line title-mid" style="top:120px">Fruit &amp;</div>
<div class="title-line title-mid" style="top:186px">Vegetable &amp;</div>
<div class="title-line title-mid" style="top:252px">Herbs &amp;</div>
<div class="title-line title-mid" style="top:318px">Spices</div>
<div class="title-line title-big" style="top:392px">CALENDAR</div>

<div class="legend"><span class="s">Summer</span><span class="a">Autumn</span><span class="w">Winter</span><span class="p">Spring</span></div>

<div class="brand"><span class="brand-dot"></span><span>Ripe Harvest Co</span></div>

<section class="chart fruits">
<table>
<colgroup><col class="name"><col><col><col><col></colgroup>
<thead><tr><th class="cat">Fruits</th><th class="season sm"><span>Summer<br>(December -<br>Febuary)</span></th><th class="season au"><span>Autumn<br>(March - May)</span></th><th class="season wi"><span>Winter<br>(June - August)</span></th><th class="season sp"><span>Spring<br>(September-<br>November)</span></th></tr></thead>
<tbody>
<tr><th>Apricot</th><td></td><td>X</td><td>X</td><td>X</td></tr>
<tr><th>Asparagus</th><td>X</td><td>X</td><td>X</td><td></td></tr>
<tr><th>Avocado</th><td class="w"></td><td></td><td></td><td></td></tr>
<tr><th>Banana</th><td></td><td></td><td>X</td><td></td></tr>
<tr><th>Blackberries</th><td></td><td></td><td>X</td><td>X</td></tr>
<tr><th>Blueberries</th><td></td><td>X</td><td>X</td><td><small>(Start Of Nov.)</small></td></tr>
<tr><th>Boysenberries</th><td></td><td>X</td><td>X</td><td>X</td></tr>
<tr><th>Cantaloupe</th><td></td><td>X</td><td>X</td><td></td></tr>
<tr><th>Cherries</th><td></td><td>X</td><td>X</td><td>X</td></tr>
<tr><th>Cherry</th><td>X</td><td>X</td><td>X</td><td></td></tr>
<tr><th>Cumquat</th><td>X</td><td></td><td></td><td></td></tr>
<tr><th>Currants</th><td></td><td>X</td><td>X</td><td>X</td></tr>
<tr><th>Custard Apple</th><td>X</td><td></td><td></td><td>X</td></tr>
<tr><th>Feijoa</th><td>X</td><td>X</td><td></td><td>X</td></tr>
<tr><th>Fig</th><td></td><td></td><td>X</td><td>X</td></tr>
<tr><th>Grapefruit</th><td></td><td></td><td></td><td></td></tr>
<tr><th>Grapes</th><td></td><td></td><td>X</td><td>X</td></tr>
<tr><th>Guava</th><td>X</td><td></td><td>X</td><td>X</td></tr>
<tr><th>Honeydew</th><td></td><td></td><td>X</td><td></td></tr>
<tr><th>Kiwi Fruit</th><td>X</td><td></td><td></td><td></td></tr>
<tr><th>Lemon</th><td></td><td></td><td></td><td></td></tr>
<tr><th>Lime</th><td>X</td><td></td><td></td><td></td></tr>
<tr><th>Loganberries</th><td></td><td>X</td><td>X</td><td>X</td></tr>
<tr><th>Loquat</th><td>X</td><td>X</td><td>X</td><td></td></tr>
<tr><th>Lychee</th><td></td><td>X</td><td>X</td><td></td></tr>
<tr><th>Mandarin Imperial</th><td>X</td><td></td><td>X</td><td>X</td></tr>
<tr><th>Mandarin<small>(Ellendale, Imperial, Murcot)</small></th><td>X</td><td>X</td><td></td><td></td></tr>
<tr><th>Mango</th><td></td><td></td><td>X</td><td></td></tr>
<tr><th>Mangosteen</th><td>X</td><td></td><td>X</td><td>X</td></tr>
<tr><th>Mulberries</th><td></td><td>X</td><td>X</td><td></td></tr>
<tr><th>Nashi</th><td>X</td><td></td><td>X</td><td>X</td></tr>
<tr><th>Nectarine</th><td></td><td>X</td><td>X</td><td>X</td></tr>
<tr><th>Orange Valencia</th><td></td><td>X</td><td>X</td><td>X</td></tr>
<tr><th>Orange(Blood, Navel, Seville)</th><td>X</td><td>X</td><td></td><td></td></tr>
<tr><th>Orange(Navel, Valencia)</th><td>X</td><td></td><td>X</td><td>X</td></tr>
<tr><th>Papaya</th><td>X</td><td></td><td>X</td><td></td></tr>
<tr><th>Passionfruit</th><td></td><td></td><td>X</td><td>X</td></tr>
<tr><th>Peach</th><td></td><td></td><td></td><td></td></tr>
<tr><th>Peach</th><td></td><td></td><td>X</td><td>X</td></tr>
<tr><th>Pear Corella</th><td>X</td><td>X</td><td>X</td><td></td></tr>
<tr><th>Pear Nashi</th><td>X</td><td></td><td></td><td>X</td></tr>
<tr><th>Pepino</th><td>X</td><td>X</td><td>X</td><td></td></tr>
<tr><th>Persimmon</th><td>X</td><td></td><td></td><td>X</td></tr>
<tr><th>Pineapple</th><td></td><td>X</td><td></td><td></td></tr>
<tr><th>Plum</th><td></td><td></td><td>X</td><td>X</td></tr>
<tr><th>Pomegranate</th><td>X</td><td></td><td>X</td><td>X</td></tr>
<tr><th>Prickly Pear</th><td>X</td><td></td><td>X</td><td>X</td></tr>
<tr><th>Quince</th><td>X</td><td></td><td></td><td>X</td></tr>
<tr><th>Rambutan</th><td>X</td><td></td><td></td><td>X</td></tr>
<tr><th>Raspberries</th><td></td><td></td><td>X</td><td>X</td></tr>
<tr><th>Rhubarb</th><td></td><td></td><td></td><td></td></tr>
<tr><th>Rockmelon</th><td>X</td><td></td><td>X</td><td>X</td></tr>
<tr><th>Starfruit</th><td>X</td><td>X</td><td>X</td><td></td></tr>
<tr><th>Strawberries</th><td></td><td></td><td>X</td><td></td></tr>
<tr><th>Tamarillo</th><td></td><td></td><td></td><td>X</td></tr>
<tr><th>Tangelo</th><td>X</td><td>X</td><td></td><td></td></tr>
<tr><th>Watermelon</th><td></td><td>X</td><td>X</td><td></td></tr>
</tbody>
</table>
</section>

<section class="chart veg">
<table>
<colgroup><col class="name"><col><col><col><col></colgroup>
<thead><tr><th class="cat">Vegetable</th><th class="season sm"><span>Summer<br>(December -<br>Febuary)</span></th><th class="season au"><span>Autumn<br>(March - May)</span></th><th class="season wi"><span>Winter<br>(June - August)</span></th><th class="season sp"><span>Spring<br>(September-<br>November)</span></th></tr></thead>
<tbody>
<tr><th>Artichoke Jerusalem</th><td>X</td><td></td><td>X</td><td>X</td></tr>
<tr><th>Artichoke(Globe, Jerusalem)</th><td>X</td><td>X</td><td>X</td><td></td></tr>
<tr><th>Asian Greens <small>(Bok Choy, Choy Sum, GaiLaan, Wombok)</small></th><td class="w"></td><td></td><td></td><td></td></tr>
<tr><th>Asparagus</th><td></td><td>X</td><td>X</td><td>X</td></tr>
<tr><th>Avocado</th><td></td><td></td><td>X</td><td>X</td></tr>
<tr><th>Beans (Butter, Green)</th><td></td><td>X</td><td>X</td><td>X</td></tr>
<tr><th>Beans(Borlotti, Butter, Green)</th><td>X</td><td></td><td>X</td><td>X</td></tr>
<tr><th>Beans(Broad, Green)</th><td>X</td><td>X</td><td>X</td><td></td></tr>
<tr><th>Beans, Broad</th><td>X</td><td>X</td><td></td><td>X</td></tr>
<tr><th>Beetroot</th><td>X</td><td></td><td>X</td><td>X</td></tr>
<tr><th>Bokchoy</th><td>X</td><td></td><td>X</td><td>X</td></tr>
<tr><th>Broccoli</th><td>X</td><td></td><td></td><td></td></tr>
<tr><th>Broccolini</th><td>X</td><td>X</td><td></td><td>X</td></tr>
<tr><th>Brussels Sprouts</th><td>X</td><td></td><td></td><td></td></tr>
<tr><th>Brussels Sprouts</th><td>X</td><td></td><td></td><td></td></tr>
<tr><th>Cabbage</th><td></td><td></td><td></td><td></td></tr>
<tr><th>Capsicum</th><td></td><td></td><td>X</td><td></td></tr>
<tr><th>Carrot</th><td></td><td></td><td></td><td></td></tr>
<tr><th>Cauliflower</th><td>X</td><td></td><td></td><td></td></tr>
<tr><th>Celeriac</th><td>X</td><td>X</td><td></td><td>X</td></tr>
<tr><th>Celery</th><td></td><td></td><td></td><td></td></tr>
<tr><th>Choko</th><td>X</td><td></td><td></td><td></td></tr>
<tr><th>Corn</th><td></td><td></td><td>X</td><td></td></tr>
<tr><th>Cucumber</th><td></td><td></td><td>X</td><td></td></tr>
<tr><th>Daikon</th><td></td><td></td><td>X</td><td></td></tr>
<tr><th>Eggplant</th><td></td><td></td><td>X</td><td></td></tr>
<tr><th>Fennel</th><td>X</td><td></td><td></td><td></td></tr>
<tr><th>Horseradish</th><td>X</td><td>X</td><td></td><td>X</td></tr>
<tr><th>Kale</th><td>X</td><td>X</td><td></td><td>X</td></tr>
<tr><th>Kohlrabi</th><td>X</td><td>X</td><td></td><td>X</td></tr>
<tr><th>Leek</th><td></td><td></td><td></td><td></td></tr>
<tr><th>Lettuce</th><td></td><td></td><td></td><td></td></tr>
<tr><th>Mushroom(Field, Pine, Slippery Jacks)</th><td>X</td><td></td><td>X</td><td>X</td></tr>
<tr><th>Mushrooms</th><td>X</td><td>X</td><td></td><td></td></tr>
<tr><th>Okra</th><td></td><td></td><td></td><td></td></tr>
<tr><th>Onion</th><td></td><td></td><td></td><td></td></tr>
<tr><th>Onion Spring</th><td></td><td></td><td></td><td></td></tr>
<tr><th>Parsnip</th><td>X</td><td></td><td></td><td></td></tr>
<tr><th>Peas</th><td></td><td></td><td></td><td></td></tr>
<tr><th>Peas, Snow</th><td>X</td><td>X</td><td></td><td>X</td></tr>
<tr><th>Potato</th><td></td><td></td><td></td><td></td></tr>
<tr><th>Pumpkin</th><td>X</td><td></td><td></td><td></td></tr>
<tr><th>Radish</th><td></td><td></td><td></td><td></td></tr>
<tr><th>Shallot</th><td></td><td></td><td></td><td></td></tr>
<tr><th>Silverbeet</th><td></td><td></td><td></td><td></td></tr>
<tr><th>Snow Peas</th><td></td><td>X</td><td>X</td><td>X</td></tr>
<tr><th>Spinach</th><td>X</td><td></td><td></td><td></td></tr>
<tr><th>Squash</th><td></td><td></td><td>X</td><td></td></tr>
<tr><th>Sugarsnaps</th><td></td><td>X</td><td>X</td><td>X</td></tr>
<tr><th>Swede</th><td>X</td><td></td><td></td><td></td></tr>
<tr><th>Sweet Potato</th><td>X</td><td></td><td></td><td></td></tr>
<tr><th>Tomato</th><td></td><td></td><td>X</td><td></td></tr>
<tr><th>Turnip</th><td>X</td><td></td><td></td><td></td></tr>
<tr><th>Watercress</th><td></td><td></td><td>X</td><td></td></tr>
<tr><th>Witlof</th><td>X</td><td></td><td>X</td><td></td></tr>
<tr><th>Zucchini</th><td></td><td></td><td>X</td><td></td></tr>
<tr><th>Zucchini Flower</th><td></td><td>X</td><td>X</td><td>X</td></tr>
</tbody>
</table>
</section>

<section class="chart herbs">
<table>
<colgroup><col class="name"><col><col><col><col></colgroup>
<thead><tr><th class="cat">Herbs &amp; Spices</th><th class="season sm"><span>Summer<br>(December -<br>Febuary)</span></th><th class="season au"><span>Autumn<br>(March - May)</span></th><th class="season wi"><span>Winter<br>(June - August)</span></th><th class="season sp"><span>Spring<br>(September-<br>November)</span></th></tr></thead>
<tbody>
<tr><th>Basil</th><td></td><td></td><td>X</td><td></td></tr>
<tr><th>Chervil</th><td></td><td></td><td>X</td><td></td></tr>
<tr><th>Chilli</th><td></td><td></td><td>X</td><td></td></tr>
<tr><th>Chives</th><td></td><td></td><td>X</td><td></td></tr>
<tr><th>Coriander</th><td></td><td></td><td></td><td></td></tr>
<tr><th>Dill</th><td></td><td></td><td></td><td></td></tr>
<tr><th>Garlic</th><td></td><td>X</td><td>X</td><td></td></tr>
<tr><th>Ginger</th><td></td><td></td><td></td><td></td></tr>
<tr><th>Lemongrass</th><td></td><td></td><td>X</td><td></td></tr>
<tr><th>Lime, Kaffir (Leaves)</th><td></td><td></td><td>X</td><td></td></tr>
<tr><th>Mint</th><td></td><td></td><td></td><td></td></tr>
<tr><th>Oregano</th><td></td><td></td><td></td><td></td></tr>
<tr><th>Parsley</th><td></td><td></td><td></td><td></td></tr>
<tr><th>Rosemary</th><td></td><td></td><td></td><td></td></tr>
<tr><th>Sage</th><td></td><td></td><td>X</td><td></td></tr>
<tr><th>Tarragon</th><td></td><td></td><td>X</td><td></td></tr>
<tr><th>Thyme</th><td></td><td></td><td>X</td><td></td></tr>
</tbody>
</table>
</section>
</body>
</html>
```